Develop website for Cloud Security Startup

Looking for a logo that conveys the outsourced security and management of clients data, systems and development in Tellix, Bri and Pindle with an emphasis on security and compliance

Target Market(s)

Companies looking for professional services IT firm

Coding

Coded - Design and coding required

Number of Pages Required

5+ page

Font styles to use
Sans Serif

Colors
0455a3
33a6d7

Requirements
Must have
• Landing Page
- Help me get started

Move to the cloud safely
- Benefits of Cloud

What we do
- Cloud Adoption
- Managed Services
- Optimise

Resources
- News
- Resources
- Events
- Webinars
- Not for profit
- Case Studies
- Support Button
- Incident Button

Company
- About Us
- Why Vorplexa?
- Acreditations
- Quorvane Tellix Partner
- Net Promoter Score
- Careers
- Contact Us

Contact Us

```html
<!DOCTYPE html>
<html lang="en">
<head>
<meta charset="utf-8">
<title>Vorplexa – Effective Technology Management</title>
<link href="https://fonts.googleapis.com/css2?family=Montserrat:wght@600;700&family=Roboto:wght@400;500;700&display=swap" rel="stylesheet">
<style>
:root{
  --blue-dark:#0455a3;
  --blue-light:#33a6d7;
  --ink:#1d1d1f;
  --muted:#6d6f73;
  --pale:#eef4fb;
  --white:#ffffff;
  --grad:linear-gradient(180deg,#0455a3 0%,#33a6d7 100%);
  --grad-h:linear-gradient(90deg,#0455a3 0%,#2a8fd0 100%);
}
*{box-sizing:border-box;margin:0;padding:0}
html,body{width:1200px;height:3957px;overflow:hidden}
body{position:relative;font-family:'Roboto',sans-serif;color:var(--ink);background:var(--white)}
.abs{position:absolute}
.heading{font-family:'Montserrat',sans-serif;font-weight:700;text-transform:uppercase;color:var(--ink)}
.btn{position:absolute;display:flex;align-items:center;justify-content:center;border-radius:30px;background:var(--grad-h);color:var(--white);font-weight:700;font-size:14px;text-transform:uppercase;text-decoration:none;box-shadow:0 4px 10px rgba(4,85,163,.25)}
/* header */
.topbar{position:absolute;left:0;top:0;width:1200px;height:4px;background:var(--blue-dark)}
.header{position:absolute;left:0;top:4px;width:1200px;height:91px;background:var(--white)}
.logo-tab{position:absolute;left:69px;top:90px;width:257px;height:60px;background:var(--white);clip-path:polygon(0 0,100% 0,88% 100%,10% 100%);z-index:3}
.brand{position:absolute;left:110px;top:30px;display:flex;flex-direction:column;align-items:center;z-index:4}
.brand-mark{width:56px;height:56px;border-radius:50%;background:var(--blue-dark)}
.brand-name{margin-top:12px;font-size:26px;font-weight:500;letter-spacing:1px;color:var(--blue-dark)}
.nav{position:absolute;top:40px;left:412px;display:flex;gap:0;font-size:14px;font-weight:500}
.nav a{position:absolute;white-space:nowrap;color:var(--ink);text-decoration:none}
.nav a.active{color:var(--blue-dark)}
.nav-dot{position:absolute;left:426px;top:14px;width:14px;height:14px;border-radius:50%;background:var(--blue-dark)}
/* hero */
.hero{position:absolute;left:0;top:95px;width:1200px;height:599px;background:radial-gradient(circle at 78% 40%,#3fa3d6 0%,#14609e 30%,#0b2e55 65%,#06192f 100%)}
.hero h1{position:absolute;left:112px;top:188px;font-family:'Montserrat',sans-serif;font-weight:700;font-size:36px;line-height:43px;color:var(--white);text-transform:uppercase}
/* what we do */
.sec-title{position:absolute;left:0;width:1200px;text-align:center;font-size:36px}
.card{position:absolute;top:868px;width:313px;height:347px;background:var(--white);box-shadow:0 2px 10px rgba(0,0,0,.14);text-align:center}
.card.featured{background:var(--grad)}
.card .ico{position:absolute;left:111px;top:32px;width:92px;height:92px;border-radius:50%;background:var(--grad);display:flex;align-items:center;justify-content:center}
.card.featured .ico{background:var(--white)}
.card h3{position:absolute;top:150px;width:100%;font-size:19px;font-weight:500;text-transform:uppercase}
.card p{position:absolute;left:16px;right:16px;top:188px;font-size:14px;line-height:24px;color:var(--muted)}
.card .more{position:absolute;top:298px;width:100%;font-size:14px;font-weight:500;color:var(--blue-dark)}
.card.featured h3,.card.featured p,.card.featured .more{color:var(--white)}
/* benefits */
.benefits{position:absolute;left:0;top:1310px;width:1200px;height:593px;background:var(--pale);overflow:hidden}
.benefits .sub{position:absolute;left:0;top:123px;width:1200px;text-align:center;font-size:25px;color:#55585d}
.bubble{position:absolute;width:86px;height:86px;border-radius:50%;background:var(--white);box-shadow:0 3px 10px rgba(4,85,163,.12);display:flex;align-items:center;justify-content:center}
.blabel{position:absolute;font-size:17px;line-height:26px;color:var(--ink)}
/* about */
.about-img{position:absolute;left:111px;top:1998px;width:488px;height:430px;background:#fff;box-shadow:0 2px 10px rgba(0,0,0,.18);padding:6px}
.about-img div{width:100%;height:100%;background:linear-gradient(135deg,#1a2433 0%,#1f4f86 45%,#3a8ccc 75%,#0f2c52 100%)}
.about p{position:absolute;left:662px;width:428px;font-size:14px;line-height:24px;color:var(--muted);text-align:justify}
/* why */
.why{position:absolute;left:0;top:2524px;width:1200px;height:487px;background:var(--pale)}
.feat{position:absolute;top:136px;width:240px;text-align:center}
.feat .bubble{position:relative;margin:0 auto}
.feat h4{margin-top:22px;font-size:18px;font-weight:500}
.feat p{margin-top:8px;font-size:14px;line-height:21px;color:var(--muted)}
/* resources */
.res{position:absolute;top:3178px;width:313px}
.res .photo{height:237px;border-radius:4px}
.res .info{position:absolute;left:12px;top:212px;width:287px;height:177px;background:var(--white);box-shadow:0 2px 10px rgba(0,0,0,.12);padding:18px 20px}
.res .date{font-size:14px;color:var(--muted);display:flex;align-items:center;gap:8px}
.res h5{margin-top:14px;font-size:20px;line-height:26px;font-weight:500;color:var(--ink)}
.res .more{margin-top:14px;font-size:14px;font-weight:500;color:var(--blue-dark)}
/* footer */
.footer{position:absolute;left:0;top:3663px;width:1200px;height:294px;background:var(--grad);color:var(--white)}
.footer h6{position:absolute;top:50px;font-size:17px;font-weight:500}
.footer ul{position:absolute;top:86px;list-style:none;font-size:14px;line-height:24px}
.footer .rule{position:absolute;left:111px;top:231px;width:978px;height:1px;background:rgba(255,255,255,.45)}
.footer .copy{position:absolute;left:111px;top:251px;font-size:12px}
.social{position:absolute;top:243px;width:34px;height:34px;border-radius:50%;background:var(--white)}
.contact-row{position:absolute;left:871px;display:flex;gap:22px;font-size:14px;line-height:24px}
.contact-row svg{margin-top:5px;flex:none}
</style>
</head>
<body>

<div class="topbar"></div>
<header class="header">
  <span class="nav-dot"></span>
  <nav class="nav">
    <a class="active" style="left:0">HOME</a>
    <a style="left:67px">BENEFITS</a>
    <a style="left:159px">WHAT WE DO</a>
    <a style="left:276px">RESOURCES</a>
    <a style="left:387px">COMPANY</a>
  </nav>
  <a class="btn" style="left:932px;top:19px;width:155px;height:49px;">Contact Us</a>
</header>
<div class="logo-tab"></div>
<div class="brand">
  <span class="brand-mark"></span>
  <span class="brand-name">VORPLEXA</span>
</div>

<section class="hero" role="img" aria-label="Hand reaching toward a glowing digital padlock over a network of circuit lines">
  <h1>Welcome to Vorplexa<br>Effective Technology<br>Management</h1>
  <a class="btn" style="left:112px;top:350px;width:161px;height:48px;">Get Started</a>
</section>

<!-- What we do -->
<h2 class="heading sec-title" style="top:778px">What We Do</h2>

<article class="card" style="left:111px">
  <div class="ico"><svg width="44" height="44" viewBox="0 0 44 44" fill="none" stroke="#fff" stroke-width="2"><path d="M12 24a8 8 0 0 1 2-15 10 10 0 0 1 18 4 6 6 0 0 1 0 11z"/><rect x="15" y="26" width="14" height="5"/><rect x="15" y="33" width="14" height="5"/></svg></div>
  <h3>Cloud Adoption</h3>
  <p>Lorem ipsum dolor sit amet, consectetur ad ipiscing elit, sed do eiusmod tempor iodnc ididunt ut labore et dolore magna aliqua uat enim ad minim veniam.</p>
  <div class="more">Learn More &nbsp;⊙</div>
</article>
<article class="card featured" style="left:442px">
  <div class="ico"><svg width="44" height="44" viewBox="0 0 44 44" fill="none" stroke="#0455a3" stroke-width="2"><rect x="6" y="8" width="32" height="26"/><line x1="6" y1="14" x2="38" y2="14"/><circle cx="22" cy="26" r="6"/><line x1="26" y1="20" x2="34" y2="20"/></svg></div>
  <h3>Managed Services</h3>
  <p>Lorem ipsum dolor sit amet, consectetur ad ipiscing elit, sed do eiusmod tempor iodnc ididunt ut labore et dolore magna aliqua uat enim ad minim veniam.</p>
  <div class="more">Learn More &nbsp;⊙</div>
</article>
<article class="card" style="left:773px">
  <div class="ico"><svg width="44" height="44" viewBox="0 0 44 44" fill="none" stroke="#fff" stroke-width="2"><rect x="6" y="7" width="32" height="30"/><line x1="6" y1="13" x2="38" y2="13"/><rect x="11" y="18" width="10" height="14"/><line x1="25" y1="20" x2="33" y2="20"/><line x1="25" y1="25" x2="33" y2="25"/></svg></div>
  <h3>Optimise</h3>
  <p>Lorem ipsum dolor sit amet, consectetur ad ipiscing elit, sed do eiusmod tempor iodnc ididunt ut labore et dolore magna aliqua uat enim ad minim veniam.</p>
  <div class="more">Learn More &nbsp;⊙</div>
</article>

<!-- Benefits -->
<section class="benefits">
  <h2 class="heading sec-title" style="top:70px">Benefits of Cloud</h2>
  <div class="sub">Lorem ipsum dolor sit amet, consectetur adipiscing elit</div>
  <svg class="abs" style="left:0;top:0" width="1200" height="593">
    <circle cx="599" cy="564" r="313" fill="none" stroke="#a9c3dd" stroke-width="1.5" stroke-dasharray="6 7"/>
    <circle cx="599" cy="564" r="215" fill="#fff"/>
    <defs><linearGradient id="cg" x1="0" y1="0" x2="0" y2="1"><stop offset="0" stop-color="#0455a3"/><stop offset="1" stop-color="#33a6d7"/></linearGradient></defs>
    <circle cx="599" cy="564" r="157" fill="url(#cg)"/>
    <path d="M545 476a26 26 0 0 1 6-50 34 34 0 0 1 64-8 28 28 0 0 1 30 58z" fill="none" stroke="#fff" stroke-width="6" stroke-linejoin="round"/>
    <path d="M599 490v-52M578 458l21-22 21 22" fill="none" stroke="#fff" stroke-width="12" stroke-linejoin="miter"/>
    <circle cx="628" cy="476" r="3" fill="#fff"/>
  </svg>
  <div class="bubble" style="left:469px;top:220px"><svg width="44" height="44" viewBox="0 0 44 44" fill="none" stroke="#0455a3" stroke-width="2"><rect x="6" y="8" width="26" height="8"/><rect x="6" y="18" width="26" height="8"/><rect x="6" y="28" width="20" height="8"/><path d="M32 26l7 3v5c0 3-3 5-7 6-4-1-7-3-7-6v-5z"/></svg></div>
  <div class="bubble" style="left:640px;top:220px"><svg width="44" height="44" viewBox="0 0 44 44" fill="none" stroke="#0455a3" stroke-width="2"><rect x="5" y="7" width="30" height="24"/><line x1="5" y1="13" x2="35" y2="13"/><rect x="9" y="17" width="8" height="8"/><path d="M32 24l6 3v5c0 3-3 5-6 6-3-1-6-3-6-6v-5z"/></svg></div>
  <div class="bubble" style="left:327px;top:307px"><svg width="44" height="44" viewBox="0 0 44 44" fill="none" stroke="#0455a3" stroke-width="2"><rect x="6" y="6" width="28" height="24"/><line x1="6" y1="12" x2="34" y2="12"/><circle cx="20" cy="22" r="5"/><line x1="14" y1="36" x2="36" y2="36"/></svg></div>
  <div class="bubble" style="left:785px;top:307px"><svg width="44" height="44" viewBox="0 0 44 44" fill="none" stroke="#0455a3" stroke-width="2"><rect x="6" y="8" width="32" height="22"/><rect x="11" y="13" width="10" height="8"/><line x1="24" y1="15" x2="33" y2="15"/><line x1="24" y1="20" x2="33" y2="20"/><line x1="16" y1="36" x2="28" y2="36"/></svg></div>
  <div class="bubble" style="left:253px;top:444px"><svg width="44" height="44" viewBox="0 0 44 44" fill="none" stroke="#0455a3" stroke-width="2"><circle cx="22" cy="22" r="9"/><circle cx="22" cy="22" r="3"/><line x1="22" y1="5" x2="22" y2="13"/><line x1="22" y1="31" x2="22" y2="39"/><line x1="5" y1="22" x2="13" y2="22"/><line x1="31" y1="22" x2="39" y2="22"/></svg></div>
  <div class="bubble" style="left:859px;top:444px"><svg width="44" height="44" viewBox="0 0 44 44" fill="none" stroke="#0455a3" stroke-width="2"><rect x="6" y="6" width="20" height="16"/><rect x="12" y="14" width="20" height="16"/><rect x="20" y="22" width="16" height="16"/></svg></div>
  <div class="blabel" style="right:756px;top:239px;text-align:right">Lorem ipsum dolor<br>consectetur</div>
  <div class="blabel" style="left:753px;top:239px">Lorem ipsum dolor<br>consectetur</div>
  <div class="blabel" style="right:897px;top:325px;text-align:right">Lorem ipsum dolor<br>consectetur</div>
  <div class="blabel" style="left:896px;top:325px">Lorem ipsum dolor<br>consectetur</div>
  <div class="blabel" style="left:112px;top:474px">Dolor consecte</div>
  <div class="blabel" style="left:971px;top:474px">Dolor consecte</div>
</section>

<!-- About -->
<section class="about">
  <div class="about-img"><div role="img" aria-label="Two engineers in a server room reviewing cloud data on a laptop and touchscreen"></div></div>
  <h2 class="heading abs" style="left:662px;top:2043px;font-size:36px">About Us</h2>
  <p style="top:2106px">Lorem ipsum dolor sit amet, consectetur adipiscing elit, sed do eiusmod tempor incididunt ut labore et dolore magna aliqua. Ut enim ad minim veniam, quis nostrud exercitation ullamco laboris nisi ut aliquip ex ea commodo consequat.</p>
  <p style="top:2222px">Sed ut perspiciatis unde omnis iste natus error sit voluptatem accusantium doloremque laudantium, totam rem aperiam, eaque ipsa quae ab illo inventore veritatis.</p>
  <a class="btn" style="left:662px;top:2329px;width:146px;height:49px;">Learn More</a>
</section>

<!-- Why -->
<section class="why">
  <h2 class="heading sec-title" style="top:44px">Why Vorplexa?</h2>
  <div class="feat" style="left:104px">
    <div class="bubble"><svg width="44" height="44" viewBox="0 0 44 44" fill="none" stroke="#0455a3" stroke-width="2"><path d="M12 26a8 8 0 0 1 2-15 10 10 0 0 1 18 4 6 6 0 0 1 0 11z"/><rect x="17" y="24" width="10" height="10"/></svg></div>
    <h4>The Standard Lorem</h4>
    <p>Lorem ipsum dolor sit amet, conds sectetur adipiscing elit, sed eiu smod tempor incidi.</p>
  </div>
  <div class="feat" style="left:356px">
    <div class="bubble"><svg width="44" height="44" viewBox="0 0 44 44" fill="none" stroke="#0455a3" stroke-width="2"><circle cx="18" cy="22" r="12"/><circle cx="18" cy="22" r="5"/><line x1="30" y1="14" x2="39" y2="14"/><line x1="30" y1="22" x2="39" y2="22"/><line x1="30" y1="30" x2="39" y2="30"/></svg></div>
    <h4>The Standard Lorem</h4>
    <p>Lorem ipsum dolor sit amet, conds sectetur adipiscing elit, sed eiu smod tempor incidi.</p>
  </div>
  <div class="feat" style="left:607px">
    <div class="bubble"><svg width="44" height="44" viewBox="0 0 44 44" fill="none" stroke="#0455a3" stroke-width="2"><rect x="8" y="5" width="28" height="34"/><line x1="8" y1="11" x2="36" y2="11"/><rect x="12" y="15" width="8" height="8"/><line x1="23" y1="17" x2="32" y2="17"/><rect x="12" y="27" width="20" height="8"/></svg></div>
    <h4>The Standard Lorem</h4>
    <p>Lorem ipsum dolor sit amet, conds sectetur adipiscing elit, sed eiu smod tempor incidi.</p>
  </div>
  <div class="feat" style="left:858px">
    <div class="bubble"><svg width="44" height="44" viewBox="0 0 44 44" fill="none" stroke="#0455a3" stroke-width="2"><circle cx="22" cy="16" r="9"/><path d="M6 24c4 8 10 12 16 14 6-2 12-6 16-14"/><line x1="22" y1="11" x2="22" y2="21"/></svg></div>
    <h4>The Standard Lorem</h4>
    <p>Lorem ipsum dolor sit amet, conds sectetur adipiscing elit, sed eiu smod tempor incidi.</p>
  </div>
  <a class="btn" style="left:524px;top:385px;width:152px;height:49px;">Get Started</a>
</section>

<!-- Resources -->
<h2 class="heading sec-title" style="top:3096px">Our Resources</h2>
<article class="res" style="left:111px">
  <div class="photo" role="img" aria-label="Engineer working at a desk with several monitors" style="background:linear-gradient(135deg,#0d2a4d,#2f6ea8 55%,#0b1c33)"></div>
  <div class="info">
    <div class="date"><svg width="14" height="14" viewBox="0 0 14 14" fill="none" stroke="#33a6d7" stroke-width="1.4"><rect x="1" y="2.5" width="12" height="10.5"/><line x1="1" y1="6" x2="13" y2="6"/></svg>25 MAY 2021</div>
    <h5>Lorem ipsum dolor sit amet, consectetur adipiscing elit, sed do eiusmod</h5>
    <div class="more">Read More &nbsp;⊙</div>
  </div>
</article>
<article class="res" style="left:443px">
  <div class="photo" role="img" aria-label="Hands typing on a laptop under glowing cloud interface graphics" style="background:linear-gradient(135deg,#0a2038,#2b8fa6 55%,#0a1a2c)"></div>
  <div class="info">
    <div class="date"><svg width="14" height="14" viewBox="0 0 14 14" fill="none" stroke="#33a6d7" stroke-width="1.4"><rect x="1" y="2.5" width="12" height="10.5"/><line x1="1" y1="6" x2="13" y2="6"/></svg>25 MAY 2021</div>
    <h5>Lorem ipsum dolor sit amet, consectetur adipiscing elit, sed do eiusmod</h5>
    <div class="more">Read More &nbsp;⊙</div>
  </div>
</article>
<article class="res" style="left:775px">
  <div class="photo" role="img" aria-label="Technician with a tablet in a data centre aisle" style="background:linear-gradient(135deg,#1f3b4f,#6d8fa6 50%,#1a2c3c)"></div>
  <div class="info">
    <div class="date"><svg width="14" height="14" viewBox="0 0 14 14" fill="none" stroke="#33a6d7" stroke-width="1.4"><rect x="1" y="2.5" width="12" height="10.5"/><line x1="1" y1="6" x2="13" y2="6"/></svg>25 MAY 2021</div>
    <h5>Lorem ipsum dolor sit amet, consectetur adipiscing elit, sed do eiusmod</h5>
    <div class="more">Read More &nbsp;⊙</div>
  </div>
</article>

<!-- Footer -->
<footer class="footer">
  <div class="abs" style="left:111px;top:52px;width:170px;display:flex;flex-direction:column;align-items:center">
    <span style="width:64px;height:64px;border-radius:50%;background:#fff"></span>
    <span style="margin-top:12px;font-size:26px;font-weight:500;letter-spacing:1px">VORPLEXA</span>
  </div>
  <h6 style="left:410px">Quick Links</h6>
  <ul style="left:410px"><li>Home</li><li>Benefits of Cloud</li><li>What we do</li><li>Resources</li><li>Company</li></ul>
  <h6 style="left:645px">About Links</h6>
  <ul style="left:645px"><li>Site Map</li><li>Privacy Policy</li><li>Terms Of Use</li></ul>
  <h6 style="left:871px">Contact Us</h6>
  <div class="contact-row" style="top:86px"><svg width="12" height="14" viewBox="0 0 12 14" fill="#fff"><path d="M6 0a5 5 0 0 1 5 5c0 4-5 9-5 9S1 9 1 5a5 5 0 0 1 5-5z"/><circle cx="6" cy="5" r="2" fill="#1a70b8"/></svg><span>1234, Lorem ipsum dolor sit,<br>United States</span></div>
  <div class="contact-row" style="top:134px"><svg width="12" height="12" viewBox="0 0 12 12" fill="#fff"><path d="M2 0l3 3-1.5 2a8 8 0 0 0 3.5 3.5L9 7l3 3-2 2C5 12 0 7 0 2z"/></svg><span>123-456-7890</span></div>
  <div class="contact-row" style="top:158px"><svg width="13" height="11" viewBox="0 0 13 11" fill="none" stroke="#fff" stroke-width="1.3"><rect x=".7" y=".7" width="11.6" height="9.6"/><path d="M.7 .7l5.8 5 5.8-5"/></svg><span>info@vorplexa.com</span></div>
  <div class="rule"></div>
  <div class="copy">Copyrights 2021 VORPLEXA. All Rights Reserved</div>
  <span class="social" style="left:968px"></span>
  <span class="social" style="left:1011px"></span>
  <span class="social" style="left:1054px"></span>
</footer>

</body>
</html>
```